Marwick Family Chiropractic Stationary

The letterhead and business card must have our logo.
We would like to see the logo used in different ways ( It can be expanded upon in the stationary.)
Please use the the same or similar colors.
Must be eye catching and memorable.
Must be easy to read

Reason: The doctor has been too busy to make any final decisions. He would like to give himself a little more time.

Target Market(s)

Chiropractic Healthcare

Industry/Entity Type

Business

Requirements
Must have
• Dr. Leonard Marwick D.C.
Chiropractor

860-555-0183

417 Birchfield Road, 2nd Floor
Vernon, CT 06091

drmarwick@marwickspine.example
www.marwickspine.example
www.facebook.com/MarwickFamilySpine
Should not have
• should not be difficult to read

```html
<!DOCTYPE html>
<html lang="en">
<head>
<meta charset="utf-8">
<title>Marwick Family Chiropractic – Business Cards</title>
<link rel="stylesheet" href="https://fonts.googleapis.com/css2?family=Questrial&family=Arimo:wght@400;700&display=swap">
<style>
  :root {
    --backdrop: #6b3a22;
    --card-black: #000000;
    --taupe: #9a8f84;
    --taupe-dark: #85796e;
    --leaf-green: #a6cf4f;
    --leaf-dark: #3f7a2e;
    --leaf-yellow: #e3e13a;
    --trunk: #7d7268;
    --white: #ffffff;
    --ink: #1d1d1b;
  }
  * { box-sizing: border-box; margin: 0; padding: 0; }
  html, body { width: 1200px; height: 716px; overflow: hidden; }
  body { background: var(--backdrop); position: relative; font-family: "Arimo", Arial, sans-serif; }

  .card { position: absolute; width: 544px; height: 309px; border-radius: 20px; overflow: hidden; }
  .card--front { left: 43px; top: 36px; background: var(--card-black); }
  .card--logo-dark { left: 619px; top: 34px; background: var(--card-black); }
  .card--pattern { left: 43px; top: 371px; background: var(--card-black); }
  .card--logo-taupe { left: 619px; top: 368px; background: var(--taupe-dark); }

  .brand { position: absolute; left: 0; right: 0; text-align: center; font-family: "Questrial", sans-serif; color: var(--leaf-green); }
  .brand__mark { display: block; margin: 0 auto 8px; border-radius: 50%; background: var(--leaf-green); }

  /* front card */
  .front__brand { top: 36px; font-size: 22px; letter-spacing: 1px; line-height: 1.15; }
  .front__brand .brand__mark { width: 64px; height: 64px; }
  .front__band { position: absolute; left: 0; right: 0; top: 181px; height: 93px; background: var(--taupe); }
  .front__name { position: absolute; right: 272px; top: 27px; text-align: right; color: var(--white); font-size: 14px; font-weight: 700; letter-spacing: -0.2px; }
  .front__role { display: block; font-weight: 400; font-size: 13px; margin-top: 4px; }
  .front__divider { position: absolute; left: 280px; top: 16px; width: 1px; height: 52px; background: var(--white); }
  .contact { position: absolute; left: 290px; top: 6px; list-style: none; color: var(--white); font-size: 13px; line-height: 21.5px; }
  .contact li { display: flex; align-items: center; gap: 6px; }
  .contact svg { width: 10px; height: 10px; fill: var(--white); flex: none; }
  .front__footer { position: absolute; left: 0; right: 0; top: 274px; bottom: 0; background: var(--leaf-green); text-align: center; line-height: 35px; color: var(--ink); font-size: 14px; font-weight: 700; }
  .front__footer span { font-weight: 400; }

  /* logo cards */
  .logo-card__brand { top: 82px; font-size: 30px; line-height: 1.2; }
  .logo-card__brand .brand__mark { width: 90px; height: 90px; margin-bottom: 14px; }
  .card--logo-taupe .brand { color: var(--white); }
  .card--logo-taupe .brand__mark { background: var(--white); }
  .web { position: absolute; left: 0; right: 0; bottom: 25px; text-align: center; color: var(--white); font-size: 15px; letter-spacing: 2.5px; font-family: "Questrial", sans-serif; }

  /* pattern card */
  .pattern-fill { position: absolute; inset: 0; background: radial-gradient(circle at 50% 50%, #1a1d10 0%, #0a0a06 100%); }
  .pattern__brand { top: 92px; font-size: 70px; font-weight: 400; letter-spacing: 2px; line-height: 1; }
  .pattern__sub { position: absolute; left: 0; right: 0; top: 160px; text-align: center; font-family: "Questrial", sans-serif; color: var(--taupe); font-size: 29px; letter-spacing: 1px; }
</style>
</head>
<body>

<section class="card card--front">
  <div class="brand front__brand">
    <span class="brand__mark"></span>
    Marwick Family Chiropractic
  </div>
  <div class="front__band">
    <p class="front__name">Dr. Leonard Marwick D.C.<span class="front__role">Chiropractor</span></p>
    <div class="front__divider"></div>
    <ul class="contact">
      <li><svg viewBox="0 0 10 10"><path d="M2 0h2l1 3-1.3 1a5 5 0 0 0 2.3 2.3L7 5l3 1v2a2 2 0 0 1-2 2A8 8 0 0 1 0 2a2 2 0 0 1 2-2z"/></svg>860-555-0183</li>
      <li><svg viewBox="0 0 10 10"><path d="M0 2h10v6H0z M0 2l5 3 5-3" stroke="#9a8f84" stroke-width="0.8"/></svg>mymarwick@marwickspine.example</li>
      <li><svg viewBox="0 0 10 10"><circle cx="5" cy="5" r="4.5"/></svg>www.marwickspine.example</li>
      <li><svg viewBox="0 0 10 10"><rect width="10" height="10" rx="1.5"/></svg>MarwickFamilySpine</li>
    </ul>
  </div>
  <div class="front__footer">Dr. Leonard Marwick D.C., <span>Chiropractor</span></div>
</section>

<section class="card card--logo-dark">
  <div class="brand logo-card__brand">
    <span class="brand__mark"></span>
    Marwick Family Chiropractic
  </div>
  <p class="web">www.marwickspine.example</p>
</section>

<section class="card card--pattern">
  <div class="pattern-fill" role="img" aria-label="Repeating pattern of small leafy trees on black"></div>
  <div class="brand pattern__brand">MARWICK</div>
  <p class="pattern__sub">FAMILY CHIROPRACTIC</p>
  <p class="web">www.marwickspine.example</p>
</section>

<section class="card card--logo-taupe">
  <div class="brand logo-card__brand">
    <span class="brand__mark"></span>
    Marwick Family Chiropractic
  </div>
  <p class="web">www.marwickspine.example</p>
</section>

</body>
</html>
```